Residential Mortgage Leader needs Wordpress Design

Looking for a home page website design for a client. We develop using the WordPress platform and would prefer the design be at least loosely based on an existing WordPress template. Attached files have many notes from our creative brief with client. The site must be responsive. Approved, basic wireframe attached. There is room for interpretation.

Existing web site: http://www.marisolkettering.example/

The Marisol Kettering Team relies on strong systems to deliver an on-time, done-right, friendly experience. Marisol offers mortgages and refinancing services throughout the United States. She is a successful Brookvale Funding agent who strives to be an active part of her community. She would like to focus the site on her team, rather than just her.

Difference makers...
When you work with the Marisol Kettering team you get a high level of expertise and a friendly experience.

She has amazing credentials. Marisol is widely recognized as a top producer for her company, and has earned a number of awards and honors for her customer service.

Marisol's team is very engaged and enjoys sharing social comments or photos from their community.

Imagery:
* Friendly, warm imagery, preferably of her team or an image to represent her team
* Clean and crisp
* Professional / Experts in mortgage and refinance
* Clean / Good use of white space
Updates

When possible, please use imagery from the DFW area. The client mentioned they would prefer not to see stock images. Thanks.

Amend that- creative use of stock images, however, is fine. A few designs have used stock imagery, but in a well-considered manner.

We added some photos and graphics that are local. We are Dallas / Ft. Worth, Plano, Frisco, Texas. We also added some examples of photos to use for the "In the Community" area. Stock photos of business folks just doesn't fit there. Thanks!

Target Market(s)

They service a lot of builders, but also work with homeowners. Their typical client is usually a woman searching for mortgage services online. She typically has a family and may refer her husband to Marisol's team. Keep in mind, however, they also see a number of other scenarios. Most of their clients are middle to high-end borrowers.

Industry/Entity Type

It Company

Requirements
Must have
• Design should be developed using program such as Photoshop or Fireworks or Illustrator as last preference. Ideally, the design would be based on an existing responsive WordPress theme, which we would customize. You must include the name of the target theme. The footer should include lots of space for disclaimers and legal language. Site navigation should include these choices: "Home, About, Builders, Mortgage Info, Approval, Blog, Contact"
Nice to have
• Blog, social media and photos area. Use of the already approved style prototype with colors and fonts (Lato- a Google font, Times New Roman and Cookie-a decorative Google font). However, we are open to interpretation.
Should not have
• Hard to read fonts or a lack of white space.

```html
<!DOCTYPE html>
<html lang="en">
<head>
<meta charset="utf-8">
<title>Marisol Kettering Team | Brookvale Funding</title>
<link href="https://fonts.googleapis.com/css2?family=Lato:wght@300;400;700&display=swap" rel="stylesheet">
<style>
:root{
  --red:#b51c1c;
  --red-dark:#6e0f0f;
  --ink:#222;
  --text:#555;
  --muted:#888;
  --light:#f0f0f0;
  --line:#d9d9d9;
  --footer:#2c2c2c;
  --footer-base:#222;
  --footer-text:#9a9a9a;
  --link:#2a9fc9;
}
*{box-sizing:border-box;margin:0;padding:0}
html,body{width:910px;height:1200px;overflow:hidden;background:#fff}
body{font-family:'Lato',sans-serif;color:var(--text);position:relative}
.abs{position:absolute}
.topbar{left:0;top:0;width:910px;height:24px;border-bottom:2px solid var(--red);font-size:8px;color:#666}
.topbar .contact{left:48px;top:7px;display:flex;align-items:center;gap:4px}
.topbar .networks{right:30px;top:7px;display:flex;gap:7px;align-items:center;color:#444;font-size:7.5px}
.header{left:0;top:24px;width:910px;height:53px;border-bottom:1px solid #e4e4e4}
.brand{left:48px;top:12px;display:flex;align-items:flex-end;gap:14px}
.brand .name{font-size:22px;color:var(--red);line-height:1;font-weight:400}
.brand .name small{display:block;font-size:6px;color:var(--muted);letter-spacing:.5px}
.brand .partner{font-size:12px;font-weight:700;color:var(--red);line-height:1}
.brand .partner small{display:block;font-size:6px;color:#333;font-weight:700}
.brand .dot{width:10px;height:10px;background:var(--red);border-radius:50%;display:inline-block;margin-left:4px}
.nav{right:30px;top:0;height:53px;display:flex}
.nav a{display:block;padding:0 15px;line-height:53px;font-size:9.5px;color:#555;text-decoration:none;position:relative}
.nav a.active{color:var(--red)}
.nav a.active:after{content:"";position:absolute;left:0;right:0;bottom:0;height:2px;background:var(--red)}
.hero{left:0;top:77px;width:910px;height:279px;background:linear-gradient(90deg,#e4e4e4,#f2f2f2 40%,#d9d9d9)}
.hero-photo{left:470px;top:77px;width:440px;height:279px;background:linear-gradient(90deg,rgba(200,200,205,0),#9aa3ad 30%,#c7b6a6 60%,#e6e3e0)}
.hero-copy{left:90px;top:135px;width:270px;text-align:center}
.hero-copy h1{font-size:28px;font-weight:400;color:var(--ink);margin-bottom:16px}
.hero-copy p{font-size:13.5px;line-height:18.5px;color:#555}
.cta{left:98px;top:260px;display:flex;align-items:center;gap:9px;font-size:12px;color:#444}
.btn{display:inline-block;height:27px;line-height:27px;padding:0 12px;color:#fff;font-size:11px;border-radius:2px}
.btn-red{background:var(--red);width:101px;text-align:center;box-shadow:0 2px 0 #7a1010}
.btn-dark{background:#4a4a4a;width:102px;text-align:center;box-shadow:0 2px 0 #222}
.band{left:0;top:356px;width:910px;height:75px;background:var(--red)}
.band h2{position:absolute;left:48px;top:14px;font-size:17.5px;font-weight:400;color:#fff}
.band p{position:absolute;left:48px;top:41px;font-size:10.5px;color:#fff}
.band .buy{position:absolute;left:749px;top:21px;width:115px;height:31px;line-height:31px;text-align:center;background:var(--red-dark);color:#fff;font-size:11px;border-radius:2px}
.credentials{left:35px;top:458px;width:213px;height:145px;border:1px solid var(--line);border-right:3px solid var(--red);padding:12px 17px;background:#fff}
.credentials h3{font-size:14px;font-weight:400;color:var(--ink);margin-bottom:7px}
.credentials .lead{font-size:11px;color:#777;margin-bottom:9px}
.credentials p{font-size:9px;line-height:14px;color:#555}
.feature{top:469px;width:180px;text-align:center}
.feature .icon{width:50px;height:50px;margin:0 auto 6px;border:2px solid #999;border-radius:4px;display:flex;align-items:center;justify-content:center}
.feature h4{font-size:12.5px;font-weight:400;color:var(--ink);margin-bottom:6px}
.feature p{font-size:7.8px;line-height:14.5px;color:#777}
.community{left:0;top:629px;width:910px;height:304px;background:var(--light)}
.community h2{position:absolute;left:0;width:916px;top:14px;text-align:center;font-size:17px;font-weight:400;color:var(--ink)}
.col-title{font-size:14px;font-weight:400;color:var(--ink);display:flex;align-items:center;gap:12px}
.col-title:after{content:"";flex:1;height:1px;background:var(--line)}
.accordion{list-style:none}
.accordion li{height:22px;margin-bottom:5px;border:1px solid var(--line);background:#f6f6f6;font-size:9.5px;color:#444;line-height:20px;padding:0 6px;position:relative}
.accordion li:after{content:"+";position:absolute;right:10px;top:0;color:#aaa;font-weight:700}
.post{display:flex;gap:14px;padding-bottom:6px;margin-bottom:8px;border-bottom:2px dotted #ccc;height:64px}
.post:last-child{border:none}
.post .net{width:29px;height:29px;background:#cfcfcf;border-radius:3px;margin:3px 0 0 10px;flex:none;position:relative}
.post .net span{position:absolute;top:32px;left:-6px;width:41px;text-align:center;font-size:6px;color:#888}
.post p{font-size:9px;line-height:14.3px;color:#555}
.post .handle{color:var(--link)}
.post .time{color:#aaa}
.gallery{display:grid;grid-template-columns:113px 113px;gap:9px}
.gallery div{height:86px;border:5px solid #fff;box-shadow:0 0 1px #ccc}
.footer{left:0;top:933px;width:910px;height:231px;background:var(--footer);color:var(--footer-text)}
.footer h3{font-size:13px;font-weight:400;color:#eee;position:absolute;top:24px}
.footer p{font-size:9.3px;line-height:14.3px}
.portrait{left:54px;top:63px;width:116px;height:124px;border:3px solid #8c8c8c;background:linear-gradient(160deg,#5a4a42,#a5847a 50%,#3a302b)}
.select{left:630px;top:132px;width:202px;height:23px;background:#555;color:#ddd;font-size:9px;font-style:italic;line-height:23px;padding-left:8px}
.select:after{content:"";position:absolute;right:8px;top:9px;border:4px solid transparent;border-top:6px solid #ccc}
.base{left:0;top:1164px;width:910px;height:36px;background:var(--footer-base);font-size:9.5px;color:#888}
.base .nets{right:90px;top:14px;font-size:7.5px;white-space:nowrap}
.base .seal{left:832px;top:9px;width:18px;height:18px;background:#bbb}
</style>
</head>
<body>

<div class="abs topbar">
  <div class="abs contact">
    <svg width="8" height="8" viewBox="0 0 24 24"><path fill="#666" d="M6.6 10.8a15 15 0 006.6 6.6l2.2-2.2a1 1 0 011-.2 11 11 0 003.6.6 1 1 0 011 1V20a1 1 0 01-1 1A17 17 0 013 4a1 1 0 011-1h3.5a1 1 0 011 1c0 1.2.2 2.5.6 3.6a1 1 0 01-.3 1z"/></svg>
    <span>Work with Us: 555-014-2290</span><span style="margin-left:5px">Email There</span>
  </div>
  <div class="abs networks">
    <span>Quillbee</span><span>Orbicle</span><span>Tessly</span><span>Portlark</span><span>Plexora</span><span>Frametta</span><span>Reelwick</span><span>Tackwell</span>
    <svg width="11" height="11" viewBox="0 0 24 24"><circle cx="10" cy="10" r="6.5" fill="none" stroke="#444" stroke-width="2.5"/><path d="M15 15l6 6" stroke="#444" stroke-width="3"/></svg>
  </div>
</div>

<div class="abs header">
  <div class="abs brand">
    <div class="name">Marisol Kettering<small>THE MARISOL KETTERING TEAM</small></div>
    <div class="partner">Brookvale Funding<span class="dot"></span><small>A Harrowgate Capital Company</small></div>
  </div>
  <nav class="abs nav">
    <a class="active">Home</a><a>About</a><a>Builders</a><a>Mortage Info</a><a>Approval</a><a>Blog</a><a>Contact</a>
  </nav>
</div>

<section class="abs hero"></section>
<div class="abs hero-photo" role="img" aria-label="Smiling businesswoman in the foreground with two colleagues reviewing papers behind her"></div>
<div class="abs hero-copy">
  <h1>Earning Your Business</h1>
  <p>The Marisol Kettering Team relies on strong systems to deliver on-time, done-right and friendly eperience</p>
</div>
<div class="abs cta"><span class="btn btn-red">Start Here</span><span>– Or –</span><span class="btn btn-dark">Get to Know Us</span></div>

<section class="abs band">
  <h2>Marisol Kettering... The only Mortage Professional you need to know!</h2>
  <p>Lorem Ipsum is simply dummy text of the printing and typesetting industry. Lorem Ipsum has been the industry's ...</p>
  <span class="buy">Purchase Now</span>
</section>

<div class="abs credentials">
  <h3>Our Credentials</h3>
  <div class="lead">A top-producer, top- not ch</div>
  <p>Lorem Ipsum is simply dummy text of the printing and typesetting industry. Lorem Ipsum has been the industry's standard dummy text ever since the 1500s been the industry's standard dummy.</p>
</div>
<div class="abs feature" style="left:261px">
  <div class="icon"><svg width="26" height="24" viewBox="0 0 26 24"><rect x="2" y="4" width="6" height="20" fill="#444"/><rect x="10" y="9" width="6" height="15" fill="#444"/><rect x="18" y="14" width="6" height="10" fill="#444"/></svg></div>
  <h4>Awards</h4>
  <p>Nam dolor neque, imperdiet eu iaculis ac, ullamcorper eget turpis. Integer mi purus, hendrerit at commodo</p>
</div>
<div class="abs feature" style="left:474px">
  <div class="icon"><svg width="22" height="22" viewBox="0 0 24 24"><path d="M12 2l3 6.5 7 .8-5.2 4.8 1.4 7L12 17.6 5.8 21l1.4-7L2 9.3l7-.8z" fill="none" stroke="#444" stroke-width="2.2"/></svg></div>
  <h4>Recognition</h4>
  <p>Nam dolor neque, imperdiet eu iaculis ac, ullamcorper eget turpis. Integer mi purus, hendrerit at commodo</p>
</div>
<div class="abs feature" style="left:686px">
  <div class="icon"><svg width="26" height="22" viewBox="0 0 26 22"><path d="M2 11l7 7L24 3" fill="none" stroke="#333" stroke-width="3.5"/></svg></div>
  <h4>Apply Now</h4>
  <p>Nam dolor neque, imperdiet eu iaculis ac, ullamcorper eget turpis. Integer mi purus, hendrerit at commodo</p>
</div>

<section class="abs community">
  <h2>Engaged In Our Community</h2>
  <div class="abs" style="left:48px;top:66px;width:305px">
    <h3 class="col-title" style="margin-bottom:14px">Blog</h3>
    <ul class="accordion">
      <li>Borrowing</li><li>Best Practices</li><li>Announcements</li><li>Resources</li><li>How to guides</li><li>Builders info</li>
    </ul>
  </div>
  <div class="abs" style="left:382px;top:66px;width:213px">
    <h3 class="col-title" style="margin-bottom:12px">Social</h3>
    <div class="post"><div class="net"><span>Quillbee</span></div><p><span class="handle">@mk_teamnews</span> Lorem Ipsum is the dummy text the printing typeset-ting instry Ipsum is has been.Lorem<br><span class="time">3 days ago</span></p></div>
    <div class="post"><div class="net"><span>Orbicle</span></div><p><span class="handle">@mk_teamnews</span> Lorem Ipsum is the dummy text the printing typeset-ting instry Ipsum is has been.Lorem<br><span class="time">3 days ago</span></p></div>
    <div class="post"><div class="net"><span>Plexora</span></div><p><span class="handle">@mk_teamnews</span> Lorem Ipsum is the dummy text the printing typeset-<br><span class="time">3 days ago</span></p></div>
  </div>
  <div class="abs" style="left:627px;top:66px;width:237px">
    <h3 class="col-title" style="margin-bottom:12px">In the Community</h3>
    <div class="gallery">
      <div role="img" aria-label="Team member in suit in an office" style="background:linear-gradient(160deg,#c9d3dc,#6d7a88)"></div>
      <div role="img" aria-label="Smiling team member in an office" style="background:linear-gradient(160deg,#e8e4df,#4f5763)"></div>
      <div role="img" aria-label="Portrait of a senior team member" style="background:linear-gradient(160deg,#3b3b3b,#a07a66 55%,#222)"></div>
      <div role="img" aria-label="Team member by a bright window checking his phone" style="background:linear-gradient(160deg,#e9f0f6,#9fb3c6 60%,#2f3b52)"></div>
    </div>
  </div>
</section>

<footer class="abs footer">
  <h3 style="left:54px">About Marisol Kettering</h3>
  <div class="abs portrait" role="img" aria-label="Portrait of Marisol Kettering, branch manager"></div>
  <div class="abs" style="left:181px;top:63px">
    <div style="font-size:13.5px;color:#ddd;margin-bottom:8px">Branch Manager</div>
    <p>Office: 555.201.4400<br>Cell: 555.318.7720<br>mkettering@brookvale.example<br>NMLS: 40219<br>418 Lantern Row, Ste.210<br>Alderbrook, TX 75099<br>Directions</p>
  </div>
  <h3 style="left:362px">Disclaimer</h3>
  <p class="abs" style="left:362px;top:63px;width:212px">In accordance with Section 326 of the USA PATRIOT Act of 2001, Brookvale Funding is required to obtain a copy of the documents used in identi-fying our new account customers. This notice is being provided to you for adequate notice given under this act.</p>
  <h3 style="left:630px">Language</h3>
  <p class="abs" style="left:630px;top:63px;width:206px">Lorem Ipsum is simply dummy text of the print-ing and typesetting industry. Lorem Ipsum has been the industry's standard dummy text ever since the 1500s been the industry's standard</p>
  <div class="abs select">English</div>
</footer>

<div class="abs base">
  <span class="abs" style="left:57px;top:13px">Marisol Kettering • Legal</span>
  <span class="abs nets">Quillbee · Orbicle · Plexora</span>
  <span class="abs seal"></span>
</div>

</body>
</html>
```